KLV Plant Services

We are a heavy diesel mechanical business with additional air con certificates, remapping engine rebuilt

Contact Information for Business Card

Company Name, Director Name, Managing Director, Contact details, email and website

Font styles to use
Serif
Script

```html
<!DOCTYPE html>
<html lang="en">
<head>
<meta charset="utf-8">
<title>KLV Plant Services – Business Card</title>
<link rel="stylesheet" href="https://fonts.googleapis.com/css2?family=Open+Sans:wght@400;600;700;800&display=swap">
<style>
  :root {
    --navy: #262373;
    --navy-deep: #1c1a5c;
    --white: #ffffff;
    --muted: #6a6a78;
    --backdrop: #e6e7ea;
    --arm-tone: #2a2a2e;
  }
  * { margin: 0; padding: 0; box-sizing: border-box; }
  html, body {
    width: 1200px; height: 900px; overflow: hidden;
    background: var(--backdrop);
    font-family: "Open Sans", sans-serif;
  }
  .canvas {
    width: 1200px; height: 900px;
    display: flex; align-items: center; justify-content: center; gap: 50px;
  }
  .card {
    position: relative;
    width: 525px; height: 300px;
    border-radius: 24px;
    overflow: hidden;
    box-shadow: 0 10px 28px rgba(20, 20, 50, 0.18);
  }
  /* Front */
  .card--front { background: var(--white); }
  .front-band { position: absolute; inset: 0; }
  .holder { position: absolute; left: 32px; top: 34px; }
  .holder__name {
    color: var(--navy); font-weight: 700; font-size: 21px; letter-spacing: 0.3px;
  }
  .holder__role { color: var(--muted); font-size: 12.5px; margin-top: 2px; }
  .contact {
    position: absolute; left: 32px; top: 146px;
    color: var(--white); font-size: 12.5px; line-height: 1.6;
    list-style: none;
  }
  .contact__address { margin-bottom: 8px; opacity: 0.9; }
  .contact__row { display: flex; align-items: center; gap: 8px; }
  .contact__row svg { width: 11px; height: 11px; fill: var(--white); flex: none; }
  .brand-name {
    position: absolute; right: 30px; top: 84px;
    display: flex; align-items: center; gap: 10px;
    color: var(--navy); font-weight: 800; line-height: 1;
  }
  .brand-name__dot {
    width: 16px; height: 16px; border-radius: 50%; background: var(--navy);
  }
  .brand-name__text { font-size: 19px; }
  .arm-illustration {
    position: absolute; right: 22px; bottom: 0;
    width: 185px; height: 130px;
    border-radius: 10px 10px 0 0;
    background: linear-gradient(160deg, #3a3a40, var(--arm-tone));
  }
  /* Back */
  .card--back {
    background: linear-gradient(150deg, var(--navy), var(--navy-deep));
    display: flex; align-items: center; justify-content: center;
  }
  .back-brand {
    display: flex; align-items: center; gap: 14px;
    color: var(--white); font-weight: 800; line-height: 1;
  }
  .back-brand__dot { width: 22px; height: 22px; border-radius: 50%; background: var(--white); }
  .back-brand__text { font-size: 32px; }
</style>
</head>
<body>
<main class="canvas">
  <section class="card card--front" aria-label="Business card front">
    <svg class="front-band" viewBox="0 0 525 300" aria-hidden="true">
      <polygon points="0,122 395,122 300,300 0,300" fill="var(--navy)"/>
    </svg>
    <div class="holder">
      <p class="holder__name">DANIEL HARTLEY</p>
      <p class="holder__role">Managing Director</p>
    </div>
    <ul class="contact">
      <li class="contact__address">P.O. Box 418 Harlow Road<br>Northvale AB, T4K 2R9</li>
      <li class="contact__row">
        <svg viewBox="0 0 24 24"><path d="M6.6 10.8a15 15 0 0 0 6.6 6.6l2.2-2.2c.3-.3.7-.4 1-.2 1.1.4 2.3.6 3.6.6.6 0 1 .4 1 1V20c0 .6-.4 1-1 1C10.6 21 3 13.4 3 4c0-.6.4-1 1-1h3.5c.6 0 1 .4 1 1 0 1.3.2 2.5.6 3.6.1.3 0 .7-.2 1z"/></svg>
        555-204-7716
      </li>
      <li class="contact__row">
        <svg viewBox="0 0 24 24"><path d="M2 5h20v14H2zM4 7v.5l8 5 8-5V7l-8 5z"/></svg>
        info@klvplantservices.com
      </li>
      <li class="contact__row">
        <svg viewBox="0 0 24 24"><circle cx="12" cy="12" r="10"/></svg>
        www.klvplantservices.com
      </li>
    </ul>
    <div class="brand-name">
      <span class="brand-name__dot"></span>
      <span class="brand-name__text">KLV Plant Services</span>
    </div>
    <div class="arm-illustration" role="img" aria-label="Silhouette of an excavator arm and bucket"></div>
  </section>

  <section class="card card--back" aria-label="Business card back">
    <div class="back-brand">
      <span class="back-brand__dot"></span>
      <span class="back-brand__text">KLV Plant Services</span>
    </div>
  </section>
</main>
</body>
</html>
```